Harborview Estates Business Card for Apartment Buildings

Create business cards for resident managers who run apartment buildings. The audience is the public who are searching for apartment rentals, and current residents who live at the apartment building. Key design element will be incorporating the company logo, however, the logo cannot dominate. The building name and manager name are more important than the logo. Current business card design leaves little room for copy, so we may need to reduce the size on the current card to allow for more space for copy.

Target Market(s)

Adults 18-65 years of age, who are looking for an apartment rental, plus current residents who live at our apartment buildings.

Industry/Entity Type

Property Management

Contact Information for Business Card

A major design element will be use of the company logo. Important property and manager contact information must be part of the design. The size of the logo will need to be reduced to make room for building and manager contact copy.

Font styles to use
Sans Serif

Colors
3176b5
000000
959595
ffffff

Requirements
Must have
• 1) Incorporate the company logo.
• 2) Use the company colors (dark blue, black/grey, over white).
• 3) FEATURE THE BUILDING NAME
• 4) FEATURE THE MANAGER NAME
• 5) The company name is less important than BUILDING and MANAGER
• 6) Manager contact information
• **SEE ATTACHED CREATIVE BRIEF**
Nice to have
• 1) Back of card logo watermark
• 2) Ability to write notes on back of carfd
Should not have
• Avoid letting the company logo dominate the card, the building name and manager are more important than the company logo.

```html
<!DOCTYPE html>
<html lang="en">
<head>
<meta charset="utf-8">
<title>Harborview Estates – Resident Manager Business Card</title>
<link href="https://fonts.googleapis.com/css2?family=Lato:wght@400;700;900&display=swap" rel="stylesheet">
<style>
  :root {
    --brand-blue: #3176b5;
    --ink: #2b2b2b;
    --grey: #959595;
    --white: #ffffff;
    --backdrop: #1b1b1d;
  }
  * { margin: 0; padding: 0; box-sizing: border-box; }
  html, body { width: 1200px; height: 963px; overflow: hidden; }
  body {
    background: var(--backdrop);
    font-family: "Lato", Arial, sans-serif;
    display: flex;
    flex-direction: column;
    align-items: center;
    justify-content: center;
    gap: 56px;
  }
  .card {
    width: 600px;
    height: 343px;
    border-radius: 18px;
    position: relative;
    overflow: hidden;
  }

  /* Front */
  .card-front {
    background: var(--white);
    display: flex;
    align-items: center;
  }
  .brand {
    width: 330px;
    display: flex;
    align-items: center;
    justify-content: center;
    gap: 12px;
  }
  .brand-dot {
    width: 34px; height: 34px;
    border-radius: 50%;
    background: var(--brand-blue);
    flex: none;
  }
  .brand-name {
    color: var(--brand-blue);
    font-weight: 900;
    font-size: 26px;
    line-height: 1.05;
    letter-spacing: 1px;
    text-transform: uppercase;
  }
  .divider {
    width: 2px;
    height: 200px;
    background: var(--brand-blue);
  }
  .contact {
    padding-left: 28px;
    color: var(--ink);
    font-size: 14px;
    line-height: 1.35;
  }
  .manager-name {
    color: var(--brand-blue);
    font-weight: 700;
    font-size: 22px;
    line-height: 1.1;
  }
  .manager-title { font-size: 14px; margin-bottom: 8px; }
  .building-name {
    color: var(--brand-blue);
    font-weight: 700;
    font-size: 17px;
  }
  .address { margin-bottom: 10px; }
  .line { display: flex; align-items: center; gap: 10px; }
  .line svg { width: 12px; height: 12px; flex: none; fill: var(--brand-blue); }

  /* Back */
  .card-back {
    background: var(--brand-blue);
    display: flex;
    flex-direction: column;
    align-items: center;
    justify-content: center;
    gap: 26px;
  }
  .card-back .brand { width: auto; }
  .card-back .brand-dot { background: var(--white); width: 44px; height: 44px; }
  .card-back .brand-name { color: var(--white); font-size: 40px; }
  .website-back {
    color: var(--white);
    font-size: 17px;
    letter-spacing: 1px;
  }
</style>
</head>
<body>

  <section class="card card-front">
    <div class="brand">
      <span class="brand-dot"></span>
      <span class="brand-name">Harborview<br>Estates LLC</span>
    </div>
    <div class="divider"></div>
    <div class="contact">
      <div class="manager-name">Marisol Ortega</div>
      <div class="manager-title">Resident Manager</div>
      <div class="building-name">Cedar Court Apartments</div>
      <div class="address">4820 Willow Street<br>Port Avalon, CA 92180</div>
      <div class="line">
        <svg viewBox="0 0 24 24" aria-hidden="true"><path d="M6.6 10.8a15 15 0 0 0 6.6 6.6l2.2-2.2a1 1 0 0 1 1-.25 11 11 0 0 0 3.6.6 1 1 0 0 1 1 1V20a1 1 0 0 1-1 1A17 17 0 0 1 3 4a1 1 0 0 1 1-1h3.5a1 1 0 0 1 1 1 11 11 0 0 0 .6 3.6 1 1 0 0 1-.25 1z"/></svg>
        555-014-2290
      </div>
      <div class="line">
        <svg viewBox="0 0 24 24" aria-hidden="true"><rect x="3" y="6" width="18" height="12" rx="2"/></svg>
        555-014-7713
      </div>
      <div class="line">
        <svg viewBox="0 0 24 24" aria-hidden="true"><rect x="6" y="2" width="12" height="20" rx="2"/></svg>
        555-014-3388
      </div>
      <div class="line">
        <svg viewBox="0 0 24 24" aria-hidden="true"><path d="M2 5h20v14H2z M2 5l10 8 10-8" fill="none" stroke="#3176b5" stroke-width="2"/></svg>
        marisol@harborviewest.com
      </div>
      <div class="line">
        <svg viewBox="0 0 24 24" aria-hidden="true"><circle cx="12" cy="12" r="9" fill="none" stroke="#3176b5" stroke-width="2"/><path d="M3 12h18M12 3c3 3 3 15 0 18M12 3c-3 3-3 15 0 18" fill="none" stroke="#3176b5" stroke-width="1.5"/></svg>
        www.harborviewest.com
      </div>
    </div>
  </section>

  <section class="card card-back">
    <div class="brand">
      <span class="brand-dot"></span>
      <span class="brand-name">Harborview<br>Estates LLC</span>
    </div>
    <div class="website-back">www.harborviewest.com</div>
  </section>

</body>
</html>
```